Letterhead Design Project

Based on the attached logo we would like have a designed of stationary.
As we are a management consulting company focused on business development dealing with C-level and one level below we new business cards.
We have decided to use KMR (Kestrel Meridian Rowe) as the business name. The legal name will be Kestrel Meridian Rowe ApS but we will brand us under KMR. The tack line is “Shaping Lasting Gains” if we need one.
For legal reasons we need to have the legal name on the letters together with the company no. (cvr. nr. 58117904)
We want to signal the following:
- Serious
- Professional
- Creating Result
- Capable of thinking out of the box and creative
- Fast reactions we will be there when needed
What we do not want to be view as is:
- To smart
- We know better
- We can fix it yesterday
Our Value Proposition is two sited:
- Increasing revenue
- Reduced sales cost or increased efficiency
Therefore, companies can call us when they want to grow or they need to be more efficient.
Our business cards should have a two sided print with the logo incl. the tack line on one side and the detailed information on the other site.
We need to have the following information on the letter head:
- Legal company name
- Cvr nr.
- Address incl. country name (Denmark)
- Main number
- Wed address
Symbols are welcome to be used to guide for the above information.
The following information are expected to be in the personal signature of the letter.
- Name
- Title
- Mobile number
- E-mail address
Updates
Some of you has requested our specific details so here they come:
- Address incl. country name (Denmark): Lyngvænget 42, 3460 Birkerød, Denmark
- Main number: +45 7081 5532
- Wed address: www.kmrhalo.com
Mobile no. are +45 xxxx xxxx or +45 2287 3104
Our e-mail looks like this: firstname.seconname@KMRHALO.COM or for me: jonas.vallgren@kmrhalo.com
We need the design (file) as finish as posible so we just need to add personal details before printing.
Please be aware that we will prefer designs where we can print the full letter incl. design. As we are communicating on e-mails with pdf versions of the letter we also need to have a design which will print on the clients printers.
Target Market(s)
C level and one level below.
Major local and international Companies.
Industry/Entity Type
Management Consulting
Font styles to use
Colors
Designer to choose colors to be used in the design.
Requirements
Must have
- Use of our logo without tack line

```html
<!DOCTYPE html>
<html lang="en">
<head>
<meta charset="utf-8">
<title>Kestrel Meridian Rowe ApS – Letterhead</title>
<link rel="stylesheet" href="https://fonts.googleapis.com/css2?family=Open+Sans:wght@400;600;700&family=Dancing+Script:wght@600&display=swap">
<style>
  :root {
    --brand-blue: #0a5fb4;
    --brand-deep: #064a91;
    --brand-light: #3f8fdc;
    --text-grey: #5a5a5a;
    --ink: #333333;
    --paper: #ffffff;
    --backdrop: #eceeef;
  }
  * { box-sizing: border-box; margin: 0; padding: 0; }
  html, body {
    width: 1200px; height: 1076px; overflow: hidden;
    background: var(--backdrop);
    font-family: "Open Sans", Arial, sans-serif;
  }
  .letterhead {
    position: absolute; left: 246px; top: 38px;
    width: 708px; height: 1000px;
    background: var(--paper);
    box-shadow: 0 4px 18px rgba(0,0,0,0.15);
    overflow: hidden;
  }
  .page-decor { position: absolute; inset: 0; width: 100%; height: 100%; }

  .header {
    position: absolute; top: 46px; right: 40px;
    display: flex; align-items: flex-start;
  }
  .company-block { text-align: right; padding-right: 14px; border-right: 1.5px solid var(--brand-blue); }
  .company-name { color: var(--brand-deep); font-weight: 700; font-size: 14px; }
  .tagline { color: var(--brand-light); font-size: 9px; font-style: italic; margin-bottom: 6px; }
  .contact-line { color: var(--brand-blue); font-size: 10.5px; line-height: 15px; display: flex; justify-content: flex-end; align-items: center; gap: 6px; }
  .contact-line svg { width: 8px; height: 10px; fill: var(--brand-blue); }
  .brand-block { padding-left: 14px; text-align: center; }
  .brand-name { color: var(--brand-blue); font-weight: 700; font-size: 40px; line-height: 44px; letter-spacing: 1px; }
  .cvr { color: var(--brand-deep); font-weight: 700; font-size: 9px; margin-top: 4px; }

  .letter-content {
    position: absolute; left: 62px; top: 200px; width: 570px;
    display: flex; flex-direction: column;
  }
  .body-copy { color: var(--text-grey); font-size: 10.5px; line-height: 13.5px; }
  .body-copy h2 { color: var(--brand-blue); font-size: 12.5px; font-weight: 700; margin-bottom: 10px; }
  .body-copy p { margin-bottom: 11px; text-align: justify; }
  .body-copy p:last-child { margin-bottom: 0; }

  .sign-off { margin-top: 32px; color: var(--text-grey); }
  .closing { font-size: 12px; line-height: 16px; }
  .signature { font-family: "Dancing Script", cursive; font-size: 20px; line-height: 26px; color: var(--ink); margin: 12px 0 8px 20px; }
  .signer-name { color: var(--brand-blue); font-weight: 700; font-size: 15px; line-height: 20px; }
  .signer-title, .signer-contact { font-size: 9px; line-height: 14px; color: var(--ink); }
</style>
</head>
<body>
<main class="letterhead">
  <svg class="page-decor" viewBox="0 0 708 1000" preserveAspectRatio="none" aria-hidden="true">
    <defs>
      <linearGradient id="swoosh" x1="0" y1="0" x2="1" y2="1">
        <stop offset="0" stop-color="#2f86d8"/>
        <stop offset="1" stop-color="#0a4f9e"/>
      </linearGradient>
    </defs>
    <path d="M0 0 H170 C70 70 20 230 0 450 Z" fill="url(#swoosh)"/>
    <path d="M0 0 H70 C30 80 10 200 0 300 Z" fill="#5aa2e6" opacity="0.45"/>
    <path d="M708 420 C690 700 630 900 500 1000 H708 Z" fill="url(#swoosh)"/>
    <path d="M708 560 C700 760 670 900 620 1000 H708 Z" fill="#0a4f9e" opacity="0.5"/>
    <rect x="330" y="990" width="378" height="10" fill="var(--brand-blue)"/>
  </svg>

  <header class="header">
    <div class="company-block">
      <div class="company-name">Kestrel Meridian Rowe ApS</div>
      <div class="tagline">Shaping Lasting Gains</div>
      <div class="contact-line">Your Address, Street No., Denmark
        <svg viewBox="0 0 8 10"><path d="M4 0a3.5 3.5 0 0 0-3.5 3.5C.5 6 4 10 4 10s3.5-4 3.5-6.5A3.5 3.5 0 0 0 4 0zm0 5a1.4 1.4 0 1 1 0-2.8A1.4 1.4 0 0 1 4 5z"/></svg>
      </div>
      <div class="contact-line">www.yourwebsite.com
        <svg viewBox="0 0 8 10"><circle cx="4" cy="5" r="3.5"/></svg>
      </div>
    </div>
    <div class="brand-block">
      <div class="brand-name">KMR</div>
      <div class="cvr">CVR. NR. 58117904</div>
    </div>
  </header>

  <div class="letter-content">
    <section class="body-copy">
      <h2>Lorem ipsum</h2>
      <p>Lorem ipsum dolor, consectetuer adipiscing elit, sed diam nonummy nibh euismod tincidunt ut laoreet dolore magna aliquam erat volutpat. Ut wisi enim ad minim veniam, quis nostrud exerci tation ullamcorper suscipit lobortis nisl ut aliquip ex ea commodo consequat. Duis autem vel eum iriure dolor in hendrerit in vulputate velit esse molestie consequat, vel illum dolore eu feugiat nulla facilisis minim</p>
      <p>Lorem ipsum dolor, consectetuer adipiscing elit, sed diam nonummy nibh euismod tincidunt ut laoreet dolore magna aliquam erat volutpat. Ut wisi enim ad minim veniam, quis nostrud exerci tation ullamcorper suscipit lobortis nisl ut aliquip ex ea commodo consequat. Duis autem vel eum iriure dolor in hendrerit in vulputate velit esse molestie consequat, vel illum dolore eu feugiat nulla facilisis minim</p>
      <p>Lorem ipsum dolor, consectetuer adipiscing elit, sed diam nonummy nibh euismod tincidunt ut laoreet dolore magna aliquam erat volutpat. Ut wisi enim ad minim veniam, quis nostrud exerci tation ullamcorper suscipit lobortis nisl ut aliquip ex ea commodo consequat. Duis autem vel eum iriure dolor in hendrerit in vulputate velit esse molestie consequat, vel illum dolore eu feugiat nulla facilisis minim</p>
      <p>Lorem ipsum dolor, consectetuer adipiscing elit, sed diam nonummy nibh euismod tincidunt ut laoreet dolore magna aliquam erat volutpat. Ut wisi enim ad minim veniam, quis nostrud exerci tation ullamcorper suscipit lobortis nisl ut aliquip ex ea commodo consequat. Duis autem vel eum iriure dolor in hendrerit in vulputate velit esse molestie consequat, vel illum dolore eu feugiat nulla facilisis minim</p>
      <p>Lorem ipsum dolor, consectetuer adipiscing elit, sed diam nonummy nibh euismod tincidunt ut laoreet dolore magna aliquam erat volutpat. Ut wisi enim ad minim veniam, quis nostrud exerci tation ullamcorper suscipit lobortis nisl ut aliquip ex ea commodo consequat. Duis autem vel eum iriure dolor in hendrerit in vulputate velit esse molestie consequat, vel illum dolore eu feugiat nulla facilisis minim</p>
      <p>Lorem ipsum dolor, consectetuer adipiscing elit, sed diam nonummy nibh euismod tincidunt ut laoreet dolore magna aliquam erat volutpat. Ut wisi enim ad minim veniam, quis nostrud exerci tation ullamcorper suscipit lobortis nisl ut aliquip ex ea commodo consequat. Duis autem vel eum iriure dolor in hendrerit in vulputate velit esse molestie consequat, vel illum dolore eu feugiat nulla facilisis minim</p>
      <p>Lorem ipsum dolor, consectetuer adipiscing elit, sed diam nonummy nibh euismod tincidunt ut laoreet dolore magna aliquam erat volutpat. Ut wisi enim ad minim veniam, quis nostrud exerci tation ullamcorper suscipit lobortis nisl ut aliquip ex ea commodo consequat. Duis autem vel eum iriure dolor in hendrerit in vulputate velit esse molestie consequat, vel illum dolore eu feugiat nulla facilisis minim</p>
      <p>Lorem ipsum dolor, consectetuer adipiscing elit, sed diam nonummy nibh euismod tincidunt ut laoreet dolore magna aliquam erat volutpat. Ut wisi enim ad minim veniam.</p>
    </section>

    <section class="sign-off">
      <div class="closing">Yours Sincerly,</div>
      <div class="signature">Yours Signature</div>
      <div class="signer-name">Your full name</div>
      <div class="signer-title">Managing Director</div>
      <div class="signer-contact">(00) 00-00-00-00</div>
      <div class="signer-contact">yourname@yourwebsite.com</div>
    </section>
  </div>
</main>
</body>
</html>
```